Vodka Bottle Label - Luma Vodka

I need a bottle label for a vodka I'd like to make called Luma Vodka.
I would like a label that looks elegant and fresh. I would like some mountains and colours to be red and white. Open to other colours being added but not too colourful. "Luma" means fresh, dawn in polish, i would like if mountains or something extra was added to the label too. I would like the Luma Vodka name not to be too small.
The vodka is made in australia and is 37%.

I would love to have a little bit of gold colour in the label!

I will provide the back label words when completing my decision.

i'd like to make it more simple and less european looking. More australian.

I saw a bottle like this and i did like the concept.

https://www.tallgumcellars.com.au/spirits/qrnt-vodka-range?srsltid=ZtqWXkelmaHuP31-ra-m7s92xudhfew_pT8eWnGBbRTxLsb3hTyQsdGaqYt

Target Market(s)

Vodka Drinkers

Industry/Entity Type

Alcohol

Colors
EB3D1F
EC4F4E
F09395
F8D3D4
FCEDEE

Requirements
Must have
• red and white colours incorporated, mountains or freshness on it.
Nice to have
• Fresh and clean look. Classy

```html
<!DOCTYPE html>
<html lang="en">
<head>
<meta charset="utf-8">
<title>Luma Vodka – Label</title>
<link rel="stylesheet" href="https://fonts.googleapis.com/css2?family=Cormorant+Garamond:wght@300;400&family=Josefin+Sans:wght@300;400;600&display=swap">
<style>
  :root {
    --page: #eef0f7;
    --label-red: #e6394d;
    --label-pink: #f0677a;
    --frame-line: #fcedee;
    --label-text: #ffffff;
    --band-violet: #4c4fa3;
    --peak-blue: #3c86d6;
    --peak-navy: #1f2c78;
    --peak-shadow: #3a2034;
    --mark-red: #ec4f4e;
  }
  html, body {
    margin: 0;
    padding: 0;
    width: 1200px;
    height: 2562px;
    overflow: hidden;
    background: var(--page);
  }
  .canvas { display: block; width: 1200px; height: 2562px; }
  .label-caps {
    font-family: "Josefin Sans", sans-serif;
    fill: var(--label-text);
  }
  .label-name {
    font-family: "Cormorant Garamond", serif;
    font-weight: 300;
    fill: var(--label-text);
  }
  .mark-name {
    font-family: "Cormorant Garamond", serif;
    font-weight: 300;
    fill: var(--mark-red);
  }
  .mark-sub {
    font-family: "Josefin Sans", sans-serif;
    font-weight: 300;
    fill: var(--mark-red);
  }
</style>
</head>
<body>
<svg class="canvas" viewBox="0 0 1200 2562" xmlns="http://www.w3.org/2000/svg">
  <defs>
    <linearGradient id="labelFill" x1="0" y1="0" x2="1" y2="0">
      <stop offset="0" stop-color="var(--label-pink)"/>
      <stop offset="0.5" stop-color="var(--label-red)"/>
      <stop offset="1" stop-color="var(--label-pink)"/>
    </linearGradient>
    <linearGradient id="peakFill" x1="0" y1="0" x2="0" y2="1">
      <stop offset="0" stop-color="var(--peak-blue)" stop-opacity="0"/>
      <stop offset="0.12" stop-color="var(--peak-blue)"/>
      <stop offset="0.55" stop-color="var(--peak-navy)"/>
      <stop offset="0.85" stop-color="var(--peak-shadow)"/>
      <stop offset="1" stop-color="var(--label-red)" stop-opacity="0"/>
    </linearGradient>
    <clipPath id="labelShape">
      <path d="M599 810 L799 880 L799 1530 L599 1600 L399 1530 L399 880 Z"/>
    </clipPath>
  </defs>

  <g class="label">
    <path class="label-body" d="M599 810 L799 880 L799 1530 L599 1600 L399 1530 L399 880 Z" fill="url(#labelFill)"/>
    <path class="label-frame" d="M599 826 L750 878 Q758 900 785 904 L785 1506 Q758 1510 750 1532 L599 1584 L448 1532 Q440 1510 413 1506 L413 904 Q440 900 448 878 Z" fill="none" stroke="var(--frame-line)" stroke-width="1.5"/>

    <text class="label-caps" x="599" y="953" font-size="15" font-weight="400" letter-spacing="6" text-anchor="middle">HANDCRAFTED</text>

    <g clip-path="url(#labelShape)">
      <rect class="mountain-art" role="img" aria-label="Watercolour mountain range in blue and navy reflected over a dark treeline" x="399" y="1000" width="400" height="330" fill="url(#peakFill)"/>
      <polygon class="region-band" points="399,1418 799,1312 799,1384 399,1490" fill="var(--band-violet)"/>
    </g>

    <text class="label-name" x="599" y="1250" font-size="96" letter-spacing="10" text-anchor="middle">LUMA</text>
    <text class="label-caps" x="599" y="1298" font-size="34" font-weight="300" letter-spacing="9" text-anchor="middle">VODKA</text>

    <text class="label-caps" x="599" y="1412" font-size="24" font-weight="300" letter-spacing="7" text-anchor="middle" transform="rotate(-14.9 599 1404)">AUSTRALIA</text>

    <text class="label-caps" x="599" y="1512" font-size="14" font-weight="400" letter-spacing="5" text-anchor="middle">GLUTEN-FREE</text>
    <text class="label-caps" x="599" y="1543" font-size="19" font-weight="600" letter-spacing="1" text-anchor="middle">37% ALC/ 70 CL</text>
  </g>

  <g class="wordmark">
    <text class="mark-name" x="600" y="2250" font-size="110" letter-spacing="12" text-anchor="middle">LUMA</text>
    <text class="mark-sub" x="600" y="2312" font-size="40" letter-spacing="14" text-anchor="middle">VODKA</text>
  </g>
</svg>
</body>
</html>
```